Dovecote Realty

Business cards for 4 people

They need to say for all
87 Tarrow Quay, Boston MA 02114

Each person will have their own personal information
We would like gold embossing for the name of the company
Marla is the blonde sitting in the chair smiling her information should be on the back of the card with her name and information
Should say for slogan classic pattern, elevated experience
grace@dovecoteprops.com
(413) 555-0182

Odette is the brunette with wavy hair in the tan suit odette@dovecoteprops.com
(617) 555-0137

faith@dovecoteprops.com
(413) 555-0164
standing next to the chair

hope@dovecoteprops.com
(413) 555-0199
close up headshot

```html
<!DOCTYPE html>
<html lang="en">
<head>
<meta charset="utf-8">
<title>Dovecote Realty – Business Cards</title>
<link href="https://fonts.googleapis.com/css2?family=Open+Sans:wght@400;600;700&display=swap" rel="stylesheet">
<style>
  :root {
    --stage: #222222;
    --navy: #223154;
    --navy-emboss: #2d4170;
    --gold: #e9b55c;
    --portrait-light: #b08560;
    --portrait-dark: #6e4a30;
  }
  * { box-sizing: border-box; margin: 0; padding: 0; }
  html, body {
    width: 1200px; height: 780px; overflow: hidden;
    background: var(--stage);
    font-family: "Open Sans", Arial, sans-serif;
  }
  .stage {
    position: relative; width: 1200px; height: 780px;
    display: flex; align-items: center; justify-content: center; gap: 30px;
  }
  .card {
    position: relative; width: 540px; height: 310px;
    background: var(--navy); overflow: hidden;
  }

  /* Front */
  .brand {
    position: absolute; left: 40px; top: 30px;
    display: flex; align-items: center; gap: 12px;
  }
  .brand-mark {
    width: 44px; height: 44px; border-radius: 50%;
    border: 2px solid var(--gold);
  }
  .brand-name {
    color: var(--gold); font-weight: 600; font-size: 18px;
    letter-spacing: 0.06em; text-transform: uppercase; white-space: nowrap;
  }
  .address {
    position: absolute; left: 40px; top: 104px;
    color: var(--gold); font-size: 13px; line-height: 1.4;
  }
  .contact-list {
    position: absolute; left: 40px; top: 168px; list-style: none;
    color: var(--gold); font-size: 13px; line-height: 1.6;
  }
  .contact-list li { display: flex; align-items: center; gap: 8px; white-space: nowrap; }
  .contact-list svg { width: 12px; height: 12px; flex: none; }

  .agent {
    position: absolute; right: 30px; top: 106px; text-align: right;
    color: var(--gold);
  }
  .agent-name { font-weight: 700; font-size: 27px; line-height: 1.15; letter-spacing: 0.01em; white-space: nowrap; }
  .agent-title { font-size: 12px; margin-top: 2px; white-space: nowrap; }
  .accent-bar {
    position: absolute; right: 0; top: 110px; width: 14px; height: 50px;
    background: var(--gold);
  }
  .portrait {
    position: absolute; right: 70px; bottom: 0; width: 190px; height: 128px;
    border-radius: 90px 90px 0 0;
    background: linear-gradient(170deg, var(--portrait-light), var(--portrait-dark));
  }

  /* Back */
  .emboss {
    position: absolute; inset: 0;
    display: flex; align-items: center; justify-content: center; gap: 18px;
  }
  .emboss-mark {
    width: 86px; height: 86px; border-radius: 50%;
    border: 3px solid var(--navy-emboss);
  }
  .emboss-name {
    color: var(--navy-emboss); font-weight: 600; font-size: 32px;
    letter-spacing: 0.06em; text-transform: uppercase; white-space: nowrap;
  }
</style>
</head>
<body>
<main class="stage">

  <section class="card card-front" aria-label="Business card front">
    <div class="brand">
      <span class="brand-mark"></span>
      <span class="brand-name">Dovecote Realty</span>
    </div>

    <p class="address">87 Tarrow Quay,<br>Boston MA 02114</p>

    <ul class="contact-list">
      <li>
        <svg viewBox="0 0 24 24" fill="var(--gold)"><path d="M6.6 10.8a15.2 15.2 0 0 0 6.6 6.6l2.2-2.2a1 1 0 0 1 1-.25 11.4 11.4 0 0 0 3.6.57 1 1 0 0 1 1 1V20a1 1 0 0 1-1 1A17 17 0 0 1 3 4a1 1 0 0 1 1-1h3.5a1 1 0 0 1 1 1c0 1.25.2 2.45.57 3.57a1 1 0 0 1-.25 1z"/></svg>
        (617) 555-0137
      </li>
      <li>
        <svg viewBox="0 0 24 24" fill="none" stroke="var(--gold)" stroke-width="2"><circle cx="12" cy="12" r="9"/><path d="M3 12h18M12 3c3 3.5 3 14.5 0 18M12 3c-3 3.5-3 14.5 0 18"/></svg>
        www.dovecoteprops.com
      </li>
      <li>
        <svg viewBox="0 0 24 24" fill="none" stroke="var(--gold)" stroke-width="2"><rect x="3" y="5" width="18" height="14" rx="1"/><path d="M3 6l9 7 9-7"/></svg>
        odette@dovecoteprops.com
      </li>
    </ul>

    <div class="agent">
      <h1 class="agent-name">Odette Lanier</h1>
      <p class="agent-title">Real Estate Advisor and Sales Manager</p>
    </div>
    <span class="accent-bar"></span>

    <div class="portrait" role="img" aria-label="Portrait photo of the agent in a tan suit"></div>
  </section>

  <section class="card card-back" aria-label="Business card back">
    <div class="emboss">
      <span class="emboss-mark"></span>
      <span class="emboss-name">Dovecote Realty</span>
    </div>
  </section>

</main>
</body>
</html>
```